Progressive European Honey Business needs minimalistic packaging design

Hello - thank you for your interest in our brief. We are Honey Plinks, a London based Honey business, importing only the best honey Europe has to offer. Our values are deeply rooted with in progressive liberal values and we are looking for minimalist packaging, which reflects that.

We are looking for a design, which dimensions fit with our packaging option (Vessio Glass Jar | HEIGHT 90mm | DIAMETER 63mm). We will require a various output files (High Resolution JPEG (CMYK Colors 300 dpi) Source File Ai, PSD, PDF, Printing files (die cut, die folding) and a 3D Mockup of the packaging for use within digital commerce platforms.

We must be able to adjust the free text on the label front and it should include the following:
Brand Name
Honey type
Limited edition No. X / 100 ( X being the number of purchase i.e. 25 / 100)
EU Honey, Single Orgin (Germany)
(c) The net weight (250g)

The back must include room for additional information (again adjustable by us) and the following:
“Unsuitable for children under 12 months”
(b) The appropriate durability declaration

In total, we are looking for
a) A front label
b) A back label
c) A seal (round) including the attached bee and logo included in the Zip file.
Do note that a) & b) can also be combined into one design as long as the symmetry on the jar stays intact.

The final design should communicate modern aesthetics, high quality, that are slightly provocative and pop off the shelves.

Hi folks, sorry for the delay in completing this project, but my business partner had a leak in his house. We planned to finalise our review today, but this will have to wait until it's no longer raining in his livingroom. Our sincere apologies!

• See branding guidelines

• Must follow the branding guideline and fonts provided as attachment

```html
<!DOCTYPE html>
<html lang="en">
<head>
<meta charset="utf-8">
<title>Honey Plinks – Back Label</title>
<link href="https://fonts.googleapis.com/css2?family=Roboto+Condensed:ital,wght@0,300;0,400;0,700;0,900;1,400;1,700&display=swap" rel="stylesheet">
<style>
  :root {
    --canvas: #ececec;
    --label-deep: #2e2230;
    --label-mid: #3f2d42;
    --ink: #ffffff;
    --ink-soft: #d9d0db;
    --accent: #e2c53a;
    --art-violet: #7a3f78;
    --art-lilac: #c7b8d6;
    --art-white: #f2eff4;
  }
  * { box-sizing: border-box; margin: 0; padding: 0; }
  html, body { width: 1200px; height: 960px; overflow: hidden; }
  body {
    background: var(--canvas);
    font-family: "Roboto Condensed", "Arial Narrow", sans-serif;
    color: var(--ink);
    position: relative;
  }
  .back-label {
    position: absolute;
    left: 220px; top: 150px;
    width: 760px; height: 660px;
    background: linear-gradient(90deg, var(--label-deep), var(--label-mid) 55%, var(--label-deep));
    overflow: hidden;
  }
  .label-artwork {
    position: absolute; left: 0; top: 0;
    width: 150px; height: 380px;
    background: linear-gradient(160deg, var(--art-white) 0%, var(--art-lilac) 40%, var(--art-violet) 80%, var(--label-mid) 100%);
    clip-path: polygon(0 0, 100% 0, 62% 45%, 80% 100%, 0 100%);
  }
  .nutrition-facts {
    position: absolute; left: 180px; top: 50px;
    width: 290px;
    border: 1.5px solid var(--ink);
    border-radius: 6px;
    padding: 8px 10px 10px;
    font-size: 13px; line-height: 1.3;
  }
  .nutrition-facts h2 { font-size: 30px; font-weight: 900; line-height: 1; letter-spacing: -0.3px; }
  .nf-rule { border-top: 1px solid var(--ink); margin: 3px 0; }
  .nf-rule.heavy { border-top-width: 9px; }
  .nf-rule.mid { border-top-width: 4px; }
  .nf-row { display: flex; justify-content: space-between; }
  .nf-row.strong { font-weight: 700; }
  .nf-row.indent { padding-left: 14px; }
  .nf-row.indent2 { padding-left: 28px; }
  .nf-calories { display: flex; justify-content: space-between; align-items: flex-end; font-weight: 900; }
  .nf-calories .label { font-size: 22px; line-height: 1; }
  .nf-calories .value { font-size: 36px; line-height: 1; }
  .nf-note { font-size: 10.5px; line-height: 1.3; margin-top: 4px; }
  .ingredients {
    position: absolute; left: 180px; top: 500px;
    width: 290px;
    font-size: 12px; line-height: 1.4; font-style: italic;
    color: var(--ink-soft);
  }
  .ingredients strong { color: var(--ink); }
  .divider-dashed {
    position: absolute; left: 505px; top: 40px; bottom: 80px;
    border-left: 1.5px dashed var(--accent);
  }
  .divider-dashed.horizontal {
    left: 505px; right: 40px; top: 140px; bottom: auto;
    border-left: none; border-top: 1.5px dashed var(--accent);
  }
  .badges {
    position: absolute; left: 540px; top: 60px;
    display: flex; gap: 18px; align-items: center;
  }
  .cert-badge { width: 54px; height: 54px; border: 3px solid var(--ink); border-radius: 50%; }
  .bpa-badge { width: 46px; height: 46px; background: var(--ink); border-radius: 50%; }
  .recycle-icon { width: 52px; height: 52px; }
  .base-line {
    position: absolute; left: 0; right: 0; bottom: 40px;
    border-top: 2px solid var(--accent);
  }
</style>
</head>
<body>
  <section class="back-label" aria-label="Honey Plinks back label">
    <div class="label-artwork" role="img" aria-label="Abstract violet and white brand artwork"></div>

    <div class="nutrition-facts">
      <h2>Nutrition Facts</h2>
      <div class="nf-rule"></div>
      <div>50 servings per container</div>
      <div class="nf-row strong"><span>Serving size</span><span>1 tsp (5g)</span></div>
      <div class="nf-rule heavy"></div>
      <div class="nf-row strong"><span>Amount per serving</span></div>
      <div class="nf-calories"><span class="label">Calories</span><span class="value">15</span></div>
      <div class="nf-rule mid"></div>
      <div class="nf-row strong"><span></span><span>% Daily Value*</span></div>
      <div class="nf-rule"></div>
      <div class="nf-row"><span><b>Total Fat</b> 0g</span><span>0%</span></div>
      <div class="nf-row indent"><span>Saturated Fat 0g</span><span>0%</span></div>
      <div class="nf-row indent"><span>Trans Fat 0g</span><span></span></div>
      <div class="nf-row"><span><b>Sodium</b> 0mg</span><span>0%</span></div>
      <div class="nf-row"><span><b>Total Carbohydrate</b> 4g</span><span>1%</span></div>
      <div class="nf-row indent"><span>Dietary Fiber 0g</span><span>0%</span></div>
      <div class="nf-row indent"><span>Total Sugars 4g</span><span></span></div>
      <div class="nf-row indent2"><span>Includes 0g Added Sugars</span><span>0%</span></div>
      <div class="nf-rule"></div>
      <div class="nf-row"><span><b>Protein</b> 0g</span><span>0%</span></div>
      <div class="nf-rule heavy"></div>
      <p class="nf-note">Not a significant source of cholesterol, vitamin D, calcium, iron and potassium. *The % Daily Value (DV) are based on a 2,000 calorie diet.</p>
    </div>

    <p class="ingredients">
      <strong>Ingredients:</strong> Raw Wildflower Honey.<br>
      Do not use if seal is broken. Best before: see lid. Store below 25°C. Honey is natural and may crystallize. Warm gently to soften.<br>
      <strong>Not suitable for infants under 12 months.</strong>
    </p>

    <div class="divider-dashed"></div>
    <div class="divider-dashed horizontal"></div>

    <div class="badges">
      <div class="cert-badge" aria-label="Certification badge"></div>
      <div class="bpa-badge" aria-label="Material badge"></div>
      <svg class="recycle-icon" viewBox="0 0 52 52" aria-label="Recycling symbol">
        <g fill="none" stroke="#ffffff" stroke-width="2.5" stroke-linejoin="round">
          <path d="M26 6 L44 38 L8 38 Z"/>
        </g>
        <g fill="#ffffff">
          <path d="M22 10 l4 -6 l4 6 z"/>
          <path d="M46 40 l-4 2 l0 -7 z"/>
          <path d="M6 40 l4 -6 l1 7 z"/>
        </g>
      </svg>
    </div>

    <div class="base-line"></div>
  </section>
</body>
</html>
```